Website for Torvel Capital - investment banking firm

We have a corporate identity (thanks to Ravinka/31842) and want to extend that into a website design.  See the attached zipped files.
We have software folks in-house to do the coding.
See the attached Project Brief & Notes for more details.  Don't worry about the actual text - lorem ipsum will be fine.
The server will be Apache.
Thank you!
Desmond

Industry/Entity Type
Investment

```html
<!DOCTYPE html>
<html lang="en">
<head>
<meta charset="utf-8">
<title>Torvel Capital</title>
<link rel="stylesheet" href="https://fonts.googleapis.com/css2?family=Open+Sans:wght@400;600&family=Arimo:wght@400&display=swap">
<style>
:root{
  --brand:#1d4f9c;
  --brand-deep:#0a4aa6;
  --ink:#333;
  --muted:#777;
  --rule:#dcdcdc;
  --nav:#111;
  --footer:#2b2b2b;
  --footer-bar:#262626;
  --footer-text:#e6e6e6;
}
*{margin:0;padding:0;box-sizing:border-box}
html,body{width:1016px;height:1200px;overflow:hidden;background:#fff}
body{position:relative;font-family:"Arimo",Arial,sans-serif;color:var(--ink)}
.abs{position:absolute}
.top-rule{left:0;top:0;width:1016px;height:3px;background:var(--brand-deep)}

.brand{left:120px;top:36px;display:flex;align-items:center;gap:12px}
.brand-dot{width:40px;height:40px;border-radius:50%;background:var(--brand)}
.brand-name{font-family:"Open Sans",sans-serif;font-weight:600;font-size:27px;letter-spacing:1px;color:var(--brand)}

.search{left:651px;top:42px;width:245px;height:25px;display:flex;border:1px solid #ddd;border-radius:2px;box-shadow:inset 0 2px 3px rgba(0,0,0,.08)}
.search-field{flex:1;font-family:"Open Sans",sans-serif;font-size:10.5px;color:#444;padding:5px 7px}
.search-btn{width:27px;background:var(--brand-deep);display:flex;align-items:center;justify-content:center;border-radius:0 2px 2px 0}

.nav{left:120px;top:107px;width:776px;height:36px;background:linear-gradient(#2a2a2a,#0c0c0c);border-bottom:3px solid var(--brand-deep);border-radius:3px 3px 0 0;display:flex;align-items:center;justify-content:space-between;padding:0 14px}
.nav a{font-family:"Open Sans",sans-serif;font-size:11.5px;color:#fff;text-decoration:none;text-transform:uppercase}
.nav a.current{color:#8fb4ee}

.hero{left:120px;top:143px;width:776px;height:346px}

.welcome-title{left:0;width:1016px;top:514px;text-align:center;font-family:"Open Sans",sans-serif;font-weight:600;font-size:14px;color:var(--brand)}
.welcome-text{left:126px;width:764px;top:547px;text-align:center;font-family:"Open Sans",sans-serif;font-size:9.6px;line-height:17.6px;color:#444}

.round-arrows{left:864px;top:613px;display:flex;gap:3px}
.round-arrows span{width:14px;height:14px;border-radius:50%;background:#999;display:flex;align-items:center;justify-content:center}

.feature{top:636px;width:260px;height:92px}
.feature-badge{left:0;top:6px;width:78px;height:78px;border-radius:50%;background:#fff;box-shadow:0 1px 4px rgba(0,0,0,.35);display:flex;align-items:center;justify-content:center}
.feature-badge div{width:66px;height:66px;border-radius:50%;background:radial-gradient(circle at 50% 35%,#3f7de0,#0e3f9c)}
.feature-rule{left:86px;top:0;width:1px;height:92px;background:var(--rule)}
.feature-title{left:93px;top:7px;font-family:"Open Sans",sans-serif;font-weight:600;font-size:13.5px;color:var(--brand)}
.feature-text{left:93px;top:32px;width:160px;font-family:"Open Sans",sans-serif;font-size:9.8px;line-height:13.6px;color:var(--muted);letter-spacing:.2px}

.shelf{left:120px;top:744px;width:776px;height:12px;background:radial-gradient(ellipse at 50% 0,rgba(0,0,0,.13),rgba(0,0,0,0) 70%)}

.section-title{font-family:"Open Sans",sans-serif;font-weight:600;font-size:14px;color:var(--brand);text-transform:uppercase}
.who-rule{left:120px;top:809px;width:500px;height:1px;background:var(--rule)}
.who-photo{left:120px;top:822px;width:190px;height:139px;background:linear-gradient(135deg,#5a5046,#c9c4bb 55%,#e8e5e0)}
.who-lead{left:319px;top:820px;width:305px;font-size:14.2px;line-height:18px;color:#222}
.who-text{left:319px;top:870px;width:306px;font-size:9.5px;line-height:16px;color:#222;text-align:justify}

.square-arrows{left:866px;top:787px;display:flex;gap:4px}
.square-arrows span{width:13px;height:13px;background:#c3cbd3;display:flex;align-items:center;justify-content:center}
.process-rule{left:655px;width:241px;height:1px;background:var(--rule)}
.quote-photo{left:656px;width:59px;height:59px;background:linear-gradient(#c9a07d,#e9cdb5)}
.quote-text{left:725px;width:172px;font-size:9.4px;line-height:14.4px;color:#666}
.quote-name{left:725px;font-family:"Open Sans",sans-serif;font-size:9.8px;color:var(--brand)}

.footer{left:0;top:998px;width:1016px;height:202px;background:var(--footer)}
.footer-bar{left:0;top:1164px;width:1016px;height:36px;background:var(--footer-bar);border-top:1px solid #3a3a3a}
.links{list-style:none;font-size:9.8px;color:var(--footer-text)}
.links li{height:23.8px}
.footer-heading{font-family:"Open Sans",sans-serif;font-size:12.5px;color:#fff;text-transform:uppercase}
.field{width:167px;height:26px;background:#fff;font-size:9.8px;color:#444;padding:7px 5px}
.signup{left:608px;top:1120px;width:74px;height:26px;background:var(--brand);color:#fff;font-family:"Open Sans",sans-serif;font-size:12.5px;display:flex;align-items:center;justify-content:center}
.address{left:759px;top:1039px;font-family:"Open Sans",sans-serif;font-size:9.8px;line-height:13.5px;color:var(--footer-text);letter-spacing:.3px}
.copyright{left:0;width:1016px;top:1176px;text-align:center;font-size:9.8px;color:#fff}
</style>
</head>
<body>
<div class="abs top-rule"></div>

<div class="abs brand">
  <div class="brand-dot"></div>
  <div class="brand-name">TORVEL CAPITAL</div>
</div>

<div class="abs search">
  <div class="search-field">Search</div>
  <div class="search-btn">
    <svg width="12" height="12" viewBox="0 0 12 12"><circle cx="4.5" cy="4.5" r="3.2" fill="none" stroke="#fff" stroke-width="1.5"/><line x1="7" y1="7" x2="11" y2="11" stroke="#fff" stroke-width="2"/></svg>
  </div>
</div>

<nav class="abs nav">
  <a class="current">Home</a><a>About</a><a>Services</a><a>Current Engagements</a><a>Completed</a><a>Transactions</a><a>Contact Us</a>
</nav>

<svg class="abs hero" viewBox="0 0 776 346" role="img" aria-label="Photo of two businesswomen talking across a desk with a laptop and lamp">
  <defs>
    <linearGradient id="heroFill" x1="0" y1="0" x2="1" y2="1">
      <stop offset="0" stop-color="#8e9c8c"/>
      <stop offset=".45" stop-color="#c9d0c6"/>
      <stop offset="1" stop-color="#b8aa9a"/>
    </linearGradient>
  </defs>
  <rect width="776" height="318" fill="url(#heroFill)"/>
  <path d="M0 314 Q388 372 776 314 L776 346 L0 346 Z" fill="#fff"/>
  <path d="M0 314 Q388 372 776 314" fill="none" stroke="#0a4aa6" stroke-width="3"/>
  <g fill="none" stroke="#fff" stroke-width="1.6">
    <circle cx="362" cy="325" r="5" fill="#555"/>
    <circle cx="379" cy="325" r="5" fill="#555"/>
    <circle cx="396" cy="325" r="5" fill="#555"/>
    <circle cx="413" cy="325" r="5" fill="#555"/>
  </g>
</svg>

<h1 class="abs welcome-title">WELCOME TO OUR COMPANY</h1>
<p class="abs welcome-text">We've developed our own proprietary valuation model that not only assesses the theoretical financial returns from an acquisition but also the risk of achieving those returns. The long-term financial success of any acquisition depends more on the growth achieved by the combined entity after acquisition than on the price paid at closing. While nobody wishes to pay more than necessary, to lead to a successful integration of the target company.</p>

<div class="abs round-arrows">
  <span><svg width="6" height="8" viewBox="0 0 6 8"><path d="M5 1 L2 4 L5 7" fill="none" stroke="#fff" stroke-width="1.6"/></svg></span>
  <span><svg width="6" height="8" viewBox="0 0 6 8"><path d="M1 1 L4 4 L1 7" fill="none" stroke="#fff" stroke-width="1.6"/></svg></span>
</div>

<section class="abs feature" style="left:120px">
  <div class="abs feature-badge"><div role="img" aria-label="Mobile phone illustration"></div></div>
  <div class="abs feature-rule"></div>
  <h2 class="abs feature-title">Strategic Advisory</h2>
  <p class="abs feature-text">Torvel Capital is an independent investment bank working for buyers in a number of indus-tries. We utilize exceptional</p>
</section>
<section class="abs feature" style="left:385px">
  <div class="abs feature-badge"><div role="img" aria-label="Light bulb illustration"></div></div>
  <div class="abs feature-rule"></div>
  <h2 class="abs feature-title">Current Engagements</h2>
  <p class="abs feature-text">Torvel Capital is an independent investment bank working for buyers in a number of indus-tries. We utilize exceptional</p>
</section>
<section class="abs feature" style="left:650px">
  <div class="abs feature-badge"><div role="img" aria-label="Rising bar chart illustration"></div></div>
  <div class="abs feature-rule"></div>
  <h2 class="abs feature-title">Completed Transactions</h2>
  <p class="abs feature-text">Torvel Capital is an independent investment bank working for buyers in a number of indus-tries. We utilize exceptional</p>
</section>

<div class="abs shelf"></div>

<h2 class="abs section-title" style="left:120px;top:782px">Who We Are</h2>
<div class="abs who-rule"></div>
<div class="abs who-photo" role="img" aria-label="Photo of hands sketching a flow chart on paper at a desk"></div>
<p class="abs who-lead">Once we have your acquisition parameters, we feed these into our software</p>
<p class="abs who-text">The criteria used to create this list can include geography, revenue targets, earning targets, margins, shareholder structure, etc. When our software has identified a qualified list, Torvel will reach out to prospective sellers.When our software has identified a qualified list, Torvel will reach out to prospective sellers. We will gather basic information during this process. At this time, we will keep</p>

<h2 class="abs section-title" style="left:655px;top:781px">Our Process</h2>
<div class="abs square-arrows">
  <span><svg width="6" height="8" viewBox="0 0 6 8"><path d="M5 1 L2 4 L5 7" fill="none" stroke="#2b3f55" stroke-width="1.6"/></svg></span>
  <span><svg width="6" height="8" viewBox="0 0 6 8"><path d="M1 1 L4 4 L1 7" fill="none" stroke="#2b3f55" stroke-width="1.6"/></svg></span>
</div>
<div class="abs process-rule" style="top:810px"></div>

<div class="abs quote-photo" style="top:824px" role="img" aria-label="Portrait photo of a team member"></div>
<p class="abs quote-text" style="top:819px">When our software has identified a quali-fied list, Torvel will reach out to prospec-tive</p>
<div class="abs quote-name" style="top:868px">-MARLO</div>
<div class="abs process-rule" style="top:890px"></div>

<div class="abs quote-photo" style="top:900px" role="img" aria-label="Portrait photo of a team member"></div>
<p class="abs quote-text" style="top:894px">When our software has identified a quali-fied list, Torvel will reach out to prospec-tive</p>
<div class="abs quote-name" style="top:943px">-MARLO</div>
<div class="abs process-rule" style="top:965px"></div>

<footer>
  <div class="abs footer"></div>
  <ul class="abs links" style="left:122px;top:1016px"><li>Home</li><li>About</li><li>News</li><li>Services</li><li>What We Do</li><li>Contact Us</li></ul>
  <ul class="abs links" style="left:236px;top:1016px"><li>Grief &amp; Healing</li><li>Resources</li><li>Plan Now</li><li>Locations</li><li>Privacy Policy</li><li>Terms &amp; Conditions</li></ul>
  <ul class="abs links" style="left:375px;top:1016px"><li>Resources</li><li>Plan Now</li><li>Locations</li><li>Privacy Policy</li><li>Terms &amp; Conditions</li></ul>

  <h3 class="abs footer-heading" style="left:517px;top:1013px">Newsletter Sign Up</h3>
  <div class="abs field" style="left:517px;top:1043px">Enter Name</div>
  <div class="abs field" style="left:515px;top:1081px">Enter Email Address</div>
  <div class="abs signup">SIGN UP</div>

  <h3 class="abs footer-heading" style="left:759px;top:1013px">Contact Us</h3>
  <p class="abs address">Hong Kong: Suite 1804<br>Harbourline Tower<br>12 - 20 Kestrel Road<br>Northpoint, Hong Kong</p>

  <div class="abs footer-bar"></div>
  <p class="abs copyright">Copyright Torvel Capital.</p>
</footer>
</body>
</html>
```